Website for Torvel Capital - investment banking firm

We have a corporate identity (thanks to Ravinka/31842) and want to extend that into a website design.  See the attached zipped files.
We have software folks in-house to do the coding.
See the attached Project Brief & Notes for more details.  Don't worry about the actual text - lorem ipsum will be fine.
The server will be Apache.
Thank you!
Desmond

Industry/Entity Type
Investment

```html
<!DOCTYPE html>
<html lang="en">
<head>
<meta charset="utf-8">
<title>Torvel Capital</title>
<link rel="stylesheet" href="https://fonts.googleapis.com/css2?family=Cinzel:wght@400;600&family=Open+Sans:wght@400;600&display=swap">
<style>
:root{
  --blue:#1d4f9b;
  --blue-dark:#143a78;
  --blue-light:#3d7bc4;
  --link:#2f7bc0;
  --ink:#222;
  --text:#444;
  --muted:#666;
  --rule:#c9cfd6;
  --grey-bg:#f2f2f2;
  --footer:#1b1b1b;
  --footer-bar:#252525;
  --white:#fff;
}
*{margin:0;padding:0;box-sizing:border-box}
html,body{width:684px;height:1200px;overflow:hidden;background:var(--white)}
body{font-family:"Open Sans",Arial,sans-serif;color:var(--text)}
.page{position:relative;width:855px;height:1500px;transform:scale(.8);transform-origin:0 0}
.abs{position:absolute}

/* header */
.site-header{left:0;top:0;width:855px;height:74px;background:linear-gradient(#eef2f7,#dbe4ee)}
.brand{left:100px;top:15px;display:flex;align-items:center;gap:12px}
.brand-square{width:38px;height:38px;background:var(--blue)}
.brand-name{font-family:"Cinzel",Georgia,serif;font-size:24px;color:var(--blue);letter-spacing:1px;white-space:nowrap}
.call{left:612px;top:16px;display:flex;gap:8px;align-items:center}
.call-label{font-family:"Cinzel",Georgia,serif;font-size:13px;color:#333;line-height:1;white-space:nowrap}
.call-number{font-family:"Cinzel",Georgia,serif;font-size:19px;color:var(--blue);line-height:1.2;white-space:nowrap}

/* nav */
.main-nav{left:0;top:74px;width:855px;height:30px;background:linear-gradient(#2458a6,#163f82);display:flex;padding-left:100px}
.main-nav a{font-family:"Cinzel",Georgia,serif;font-size:11px;color:var(--white);text-decoration:none;padding:0 12px;line-height:30px;border-right:1px solid rgba(255,255,255,.18);letter-spacing:.4px;white-space:nowrap}
.main-nav a.active{background:#4a82c5}

/* hero */
.hero{left:0;top:104px;width:855px;height:280px;background:linear-gradient(90deg,#e6e6e6,#f6f6f6 60%,#ececec)}
.hero-photo{left:0;top:0;width:420px;height:280px;background:linear-gradient(90deg,#1e1f24 0%,#3d3f46 35%,#c9ccd2 75%,rgba(236,236,236,0) 100%)}
.hero-title{left:418px;top:42px;font-family:"Cinzel",Georgia,serif;font-size:28px;font-weight:600;color:var(--blue);letter-spacing:1px;white-space:nowrap}
.hero-text{left:420px;top:84px;width:340px;font-size:15.5px;line-height:21px;color:#333}
.btn{display:inline-block;background:linear-gradient(#3a7ac2,#1f5aa0);color:var(--white);text-decoration:none;border:1px solid #1b4f8e;border-radius:2px;white-space:nowrap}
.hero-btn{left:424px;top:183px;padding:5px 14px;font-size:12px}
.dots{left:427px;top:248px;display:flex;gap:5px}
.dots span{width:10px;height:10px;border-radius:50%;background:#bbb}
.dots span.on{background:var(--blue)}

/* section titles */
.section-title{font-family:"Cinzel",Georgia,serif;font-weight:400;font-size:22px;color:var(--ink);display:flex;align-items:center;gap:12px;justify-content:center;white-space:nowrap}
.section-title em{font-style:normal;color:var(--blue)}
.section-title .line{width:120px;border-top:1px solid var(--rule);border-bottom:1px solid var(--rule);height:4px}

/* services */
.what-we-do{left:0;top:405px;width:855px}
.services{left:75px;top:452px;width:705px;display:flex}
.service{width:235px;text-align:center;position:relative}
.service + .service::before{content:"";position:absolute;left:0;top:20px;height:160px;border-left:1px solid #e4e4e4}
.service-icon{width:90px;height:90px;margin:0 auto;border-radius:50%;background:radial-gradient(circle at 40% 35%,#2a63b2,#123c7f);box-shadow:0 0 0 3px #fff,0 0 0 4px #d5d9de;display:flex;align-items:center;justify-content:center}
.service h3{font-weight:400;font-size:13.5px;color:var(--link);line-height:16px;margin-top:8px}
.service p{font-size:9.2px;line-height:12px;color:#444;margin:14px 22px 0}
.service .more{display:block;font-size:9px;color:#222;margin-top:10px;font-weight:600}

/* about */
.about{left:0;top:675px;width:855px;height:230px;background:var(--grey-bg);border-top:1px solid #e2e2e2;border-bottom:1px solid #e2e2e2}
.about-title{left:0;top:17px;width:855px}
.about-photo{left:100px;top:58px;width:189px;height:151px;border:3px solid #fff;outline:1px solid #ccc;background:linear-gradient(135deg,#cfd6de,#8e949c 55%,#2a2d34)}
.about-text{left:300px;top:56px;width:462px;font-size:8.5px;line-height:14.6px;color:#444;letter-spacing:-.05px}
.about-text p+p{margin-top:6px}
.about-btn{left:301px;top:192px;padding:2px 6px;font-size:9px;font-weight:600}

/* acquisition */
.block-title{font-family:"Cinzel",Georgia,serif;font-weight:400;font-size:14.5px;color:var(--ink);letter-spacing:.3px;padding-bottom:4px;border-bottom:1px solid var(--rule);position:relative;white-space:nowrap}
.block-title em{font-style:normal;color:var(--blue)}
.block-title::after{content:"";position:absolute;left:0;bottom:-2px;width:44px;height:3px;background:var(--blue)}
.acq{left:101px;top:935px;width:322px}
.acq-intro{font-size:9.3px;line-height:14px;color:#222;margin-top:10px}
.acq-list{display:grid;grid-template-columns:153px 160px;list-style:none;margin-top:9px;row-gap:6.6px}
.acq-list li{font-size:8.8px;color:#333;display:flex;align-items:center;gap:8px;height:14px;white-space:nowrap}
.acq-list li.hl{color:var(--link)}
.tick{width:10px;height:10px;flex:none}

/* testimonials */
.testi{left:447px;top:935px;width:313px}
.testi-photo{left:447px;top:976px;width:64px;height:64px;border-radius:50%;background:radial-gradient(circle,#9fb4c6,#5d6d7c);border:3px solid #fff;box-shadow:0 0 0 1px #bbb}
.quote{left:535px;top:969px;width:225px;height:142px;border:1px solid #d4d4d4;border-bottom:2px solid var(--blue);background:#fafafa}
.quote-mark{left:7px;top:6px;font-family:Georgia,serif;font-size:26px;color:#aaa}
.quote-text{left:14px;top:12px;width:204px;font-size:8.6px;line-height:17px;font-style:italic;color:#444;text-indent:18px}
.quote-author{left:8px;top:119px;font-size:9px;font-weight:600;color:#222}
.quote-more{right:-1px;bottom:-2px;background:var(--blue);color:#fff;font-size:9px;width:56px;height:14px;line-height:14px;padding-left:10px}
.quote-more::after{content:"›";position:absolute;right:0;top:0;width:13px;height:14px;background:var(--blue-light);text-align:center}

/* clients */
.clients{left:0;top:1152px;width:855px;height:145px;background:#f4f4f4;border-top:1px solid #e1e1e1}
.clients-tab{left:342px;top:-1px;width:165px;height:25px;background:var(--blue);clip-path:polygon(0 0,100% 0,93% 100%,7% 100%);color:#fff;font-family:"Cinzel",Georgia,serif;font-size:15px;text-align:center;line-height:24px}
.client-row{left:130px;top:43px;display:flex;gap:8px}
.client{width:113px;height:60px;background:#eaeaea;border:1px solid #dcdcdc;display:flex;align-items:center;justify-content:center;gap:6px;font-size:17px;font-weight:600;color:#555;white-space:nowrap}
.client .sq{width:11px;height:11px;border-radius:50%;background:#555}
.arrow-btn{top:64px;width:20px;height:20px;border-radius:50%;background:#fff;border:1px solid #bbb;display:flex;align-items:center;justify-content:center}

/* footer */
.site-footer{left:0;top:1297px;width:855px;height:170px;background:var(--footer)}
.footer-title{font-family:"Cinzel",Georgia,serif;font-weight:400;font-size:13.5px;color:#eee;letter-spacing:.5px;padding-bottom:7px;border-bottom:1px solid #3a3a3a;white-space:nowrap}
.quick{left:101px;top:12px;width:122px}
.quick ul{list-style:none;margin-top:6px}
.quick li{font-size:9px;color:#ddd;line-height:19.6px;padding-left:15px;position:relative;white-space:nowrap}
.quick li::before{content:"›";position:absolute;left:2px;color:#999}
.contact{left:264px;top:12px;width:385px}
.map{left:264px;top:45px;width:172px;height:109px;background:linear-gradient(135deg,#e8e4da,#cfd8de 60%,#dde2d6)}
.addr{left:447px;top:45px;width:210px;font-size:8.6px;line-height:11.5px;color:#ddd;white-space:nowrap}
.addr-row{position:relative;padding-left:18px}
.addr-row svg{position:absolute;left:0;top:1px}
.follow{left:682px;top:12px;width:80px}
.social{list-style:none;margin-top:10px}
.social li{display:flex;align-items:center;gap:9px;font-size:9px;color:#ddd;height:24px}
.social .dot{width:16px;height:16px;border-radius:50%;background:#ccc}
.footer-bar{left:0;top:1467px;width:855px;height:33px;background:var(--footer-bar);font-size:8.5px;color:#ccc}
.copy{left:104px;top:12px;white-space:nowrap}
.legal{left:628px;top:12px;white-space:nowrap}
</style>
</head>
<body>
<div class="page">

  <header class="site-header abs">
    <div class="brand abs">
      <span class="brand-square"></span>
      <span class="brand-name">TORVEL CAPITAL</span>
    </div>
    <div class="call abs">
      <svg width="26" height="28" viewBox="0 0 26 28"><path d="M5 2l5 6-3 3c2 4 5 7 9 9l3-3 6 5-3 4C11 25 2 16 1 5z" fill="#1d4f9b"/></svg>
      <div>
        <div class="call-label">CALL US TODAY</div>
        <div class="call-number">469-555-0147</div>
      </div>
    </div>
  </header>

  <nav class="main-nav abs">
    <a class="active">HOME</a><a>ABOUT</a><a>SERVICES</a><a>CURRENT ENGAGEMENTS</a><a>COMPLETED TRANSACTIONS</a><a>CONTACT US</a>
  </nav>

  <section class="hero abs">
    <div class="hero-photo abs" role="img" aria-label="Businessman in a suit drawing a rising growth chart on a glass screen"></div>
    <h1 class="hero-title abs">TORVEL CAPITAL LLC IS</h1>
    <p class="hero-text abs">Dallas-based private investment banking advisory firm that acts as an intermediary on behalf of buyers &amp; sellers of private companies.</p>
    <a class="btn hero-btn abs">LEARN MORE</a>
    <div class="dots abs"><span class="on"></span><span></span><span></span><span></span></div>
  </section>

  <h2 class="section-title what-we-do abs"><span class="line"></span><span>WHAT <em>WE DO</em></span><span class="line"></span></h2>

  <div class="services abs">
    <div class="service">
      <div class="service-icon">
        <svg width="50" height="36" viewBox="0 0 50 36"><path d="M2 10l10-6 10 4 8-4 18 8-6 14-8 6-12-4-12-8z" fill="none" stroke="#fff" stroke-width="3" stroke-linejoin="round"/></svg>
      </div>
      <h3>Buy-Side<br>Acquisitions</h3>
      <p>Lorem ipsum dolor sit amet, consectetuer adipiscing elit, sed diam nonummy nibh euism od t laoreet dolor into thwe.</p>
      <span class="more">Read More »</span>
    </div>
    <div class="service">
      <div class="service-icon">
        <svg width="46" height="44" viewBox="0 0 46 44"><text x="4" y="16" font-size="18" font-weight="700" fill="#fff" font-family="Arial">$</text><rect x="4" y="30" width="6" height="12" fill="#fff"/><rect x="13" y="24" width="6" height="18" fill="#fff"/><rect x="22" y="27" width="6" height="15" fill="#fff"/><rect x="31" y="18" width="6" height="24" fill="#fff"/><path d="M4 24l12-8 8 4 16-14" stroke="#fff" stroke-width="2.5" fill="none"/></svg>
      </div>
      <h3>Recapitalizations &amp;<br>Growth Capital Partnerships</h3>
      <p>Lorem ipsum dolor sit amet, consectetuer adipiscing elit, sed diam nonummy nibh euism od t laoreet dolor into thwe.</p>
      <span class="more">Read More »</span>
    </div>
    <div class="service">
      <div class="service-icon">
        <svg width="44" height="44" viewBox="0 0 44 44"><text x="15" y="22" font-size="22" font-weight="700" fill="#fff" font-family="Arial">$</text><path d="M4 30h10l8 4 14-8 4 2-16 12H4z" fill="#fff"/></svg>
      </div>
      <h3>Sell-Side<br>Transactions</h3>
      <p>Lorem ipsum dolor sit amet, consectetuer adipiscing elit, sed diam nonummy nibh euism od t laoreet dolor into thwe.</p>
      <span class="more">Read More »</span>
    </div>
  </div>

  <section class="about abs">
    <h2 class="section-title about-title abs"><span class="line" style="width:112px"></span><span>ABOUT <em>TORVEL CAPITAL</em></span><span class="line" style="width:112px"></span></h2>
    <div class="about-photo abs" role="img" aria-label="Business team meeting around a desk with laptop and charts"></div>
    <div class="about-text abs">
      <p>Torvel Capital's history in mergers and acquisitions traces back to 1998. We pride our selves in successfully matching buyers with sellers and enabling shareholders of all stakeholders in a transaction to prosper. We will not waste your time - this is our promise to you. We will bring only qualified opportunities to buyers. We will not proceed with a seller unless there is a real opportunity to successfully complete a transaction.</p>
      <p>Torvel Capital traces its investment banking roots to 1998 beginning with the divestiture of assets in a cross-border transaction. Since then Torvel Capital has found acquisitions for buyers in a wide range of fields including oil &amp; gas, software, niche manufacturing, agriculture, transportation, financial services. Over the years, Torvel Capital has created technologies that identify potential acquisition targets based on our clients' needs.</p>
    </div>
    <a class="btn about-btn abs">Read More »</a>
  </section>

  <section class="acq abs">
    <h2 class="block-title">CURRENT ACQUISITION <em>SEARCH INFO</em></h2>
    <p class="acq-intro">The following is a list of recent searches. Current search criteria is extensive. Please contact us for more information.</p>
    <ul class="acq-list">
      <li><svg class="tick" viewBox="0 0 10 10"><path d="M1 5l3 3 5-7" stroke="#333" stroke-width="1.4" fill="none"/></svg>Oilfield Services</li>
      <li><svg class="tick" viewBox="0 0 10 10"><path d="M1 5l3 3 5-7" stroke="#333" stroke-width="1.4" fill="none"/></svg>Food Manufacturers</li>
      <li class="hl"><svg class="tick" viewBox="0 0 10 10"><path d="M1 5l3 3 5-7" stroke="#2f7bc0" stroke-width="1.4" fill="none"/></svg>Oilfield Manufacturing</li>
      <li><svg class="tick" viewBox="0 0 10 10"><path d="M1 5l3 3 5-7" stroke="#333" stroke-width="1.4" fill="none"/></svg>Insurance MGA's</li>
      <li><svg class="tick" viewBox="0 0 10 10"><path d="M1 5l3 3 5-7" stroke="#333" stroke-width="1.4" fill="none"/></svg>Asset Managment</li>
      <li><svg class="tick" viewBox="0 0 10 10"><path d="M1 5l3 3 5-7" stroke="#333" stroke-width="1.4" fill="none"/></svg>Healthcare Providers</li>
      <li><svg class="tick" viewBox="0 0 10 10"><path d="M1 5l3 3 5-7" stroke="#333" stroke-width="1.4" fill="none"/></svg>Insurance Brokerage</li>
      <li><svg class="tick" viewBox="0 0 10 10"><path d="M1 5l3 3 5-7" stroke="#333" stroke-width="1.4" fill="none"/></svg>Medical Instrumentation</li>
      <li><svg class="tick" viewBox="0 0 10 10"><path d="M1 5l3 3 5-7" stroke="#333" stroke-width="1.4" fill="none"/></svg>3PL / Logistics</li>
      <li><svg class="tick" viewBox="0 0 10 10"><path d="M1 5l3 3 5-7" stroke="#333" stroke-width="1.4" fill="none"/></svg>Metals and Materials</li>
      <li><svg class="tick" viewBox="0 0 10 10"><path d="M1 5l3 3 5-7" stroke="#333" stroke-width="1.4" fill="none"/></svg>Special Situations</li>
      <li><svg class="tick" viewBox="0 0 10 10"><path d="M1 5l3 3 5-7" stroke="#333" stroke-width="1.4" fill="none"/></svg>Industrial Products/Services</li>
    </ul>
  </section>

  <section class="testi abs">
    <h2 class="block-title">CLIENT <em>TESTIMONIALS</em></h2>
  </section>
  <div class="testi-photo abs" role="img" aria-label="Portrait photo of the client giving the testimonial"></div>
  <blockquote class="quote abs">
    <span class="quote-mark abs">“</span>
    <p class="quote-text abs">Lorem ipsum dolor sit amet, consectetuer in adipiscing elit Sed diam nonummy nibh euismod tiidunt ut laoreet dolore magna aliqm erat volut Ut wisi enim ad minim veniam, quis nostrud exeo ullcoper suscipit lobortis nis volpat.Ut wisi enim ad minim veniam quis .</p>
    <span class="quote-author abs">- Aldo Brennan</span>
    <span class="quote-more abs">More</span>
  </blockquote>

  <section class="clients abs">
    <div class="clients-tab abs">OUR CLIENTS</div>
    <div class="arrow-btn abs" style="left:101px"><svg width="8" height="8" viewBox="0 0 8 8"><path d="M5 1L2 4l3 3" stroke="#333" stroke-width="1.5" fill="none"/></svg></div>
    <div class="client-row abs">
      <div class="client">Norvale</div>
      <div class="client"><span class="sq"></span>Keystrand</div>
      <div class="client">Pellmark</div>
      <div class="client"><span class="sq"></span>Ostrin</div>
      <div class="client">Larkwell</div>
    </div>
    <div class="arrow-btn abs" style="left:738px"><svg width="8" height="8" viewBox="0 0 8 8"><path d="M3 1l3 3-3 3" stroke="#333" stroke-width="1.5" fill="none"/></svg></div>
  </section>

  <footer class="site-footer abs">
    <div class="quick abs">
      <h3 class="footer-title">QUICK LINKS</h3>
      <ul><li>Home</li><li>About</li><li>Services</li><li>Current Engagements</li><li>Completed Transactions</li><li>Contact Us</li></ul>
    </div>
    <div class="contact abs"><h3 class="footer-title">CONTACT DETAIL</h3></div>
    <div class="map abs" role="img" aria-label="Street map showing the office location"></div>
    <div class="addr abs">
      <div class="addr-row"><svg width="9" height="12" viewBox="0 0 9 12"><path d="M4.5 0A4.5 4.5 0 0 0 0 4.5C0 8 4.5 12 4.5 12S9 8 9 4.5A4.5 4.5 0 0 0 4.5 0zm0 6.5a2 2 0 1 1 0-4 2 2 0 0 1 0 4z" fill="#ddd"/></svg>Hong Kong: Room 1804 Harbour Point Tower<br>12 - 18 Lockhart Road East<br>Wanchai, Hong Kong</div>
      <div class="addr-row" style="margin-top:5px">Dallas: 4100 Meadow Parkway, Suite 210<br>Plano, Texas 75024</div>
      <div class="addr-row" style="margin-top:11px;font-weight:600"><svg width="11" height="11" viewBox="0 0 26 28"><path d="M5 2l5 6-3 3c2 4 5 7 9 9l3-3 6 5-3 4C11 25 2 16 1 5z" fill="#ddd"/></svg>469-555-0147</div>
      <div class="addr-row" style="margin-top:13px"><svg width="11" height="8" viewBox="0 0 11 8"><rect width="11" height="8" fill="#ddd"/><path d="M0 0l5.5 4L11 0" stroke="#1b1b1b" fill="none"/></svg>info@torvelcapital.com</div>
    </div>
    <div class="follow abs">
      <h3 class="footer-title" style="border:0">FOLLOW US</h3>
      <ul class="social">
        <li><span class="dot"></span>Circlebook</li>
        <li><span class="dot"></span>Viewtube</li>
        <li><span class="dot"></span>Chirper</li>
        <li><span class="dot"></span>Worknet</li>
      </ul>
    </div>
  </footer>

  <div class="footer-bar abs">
    <span class="copy abs">© Copyright 2014 Torvel Capital. | All Rights Reserved</span>
    <span class="legal abs">Site Map &nbsp; | &nbsp; Terms &amp; Conditions</span>
  </div>

</div>
</body>
</html>
```